Brivane Management

We need a web design for a new consulting company, with clients all over the world. The company provides management consulting to the travel industry.

Logo files are attached.

Website must look very corporate and be responsive in design.

Management Consulting

```html
<!DOCTYPE html>
<html lang="en">
<head>
<meta charset="utf-8">
<title>Brivane Management</title>
<link href="https://fonts.googleapis.com/css2?family=Bitter:wght@400;500&family=Lato:wght@400;700&family=Oswald:wght@400&display=swap" rel="stylesheet">
<style>
:root{
  --navy:#15184a;
  --green:#6aab2a;
  --blue:#0a6fc2;
  --blue-dark:#0a5aa6;
  --text:#333;
  --rule:#dcdcdc;
  --band:#ebebeb;
}
*{box-sizing:border-box;margin:0;padding:0}
html,body{width:756px;height:1200px;overflow:hidden;background:#fff}
body{position:relative;font-family:"Lato",sans-serif;color:var(--text)}
.abs{position:absolute}
.header{left:0;top:0;width:756px;height:65px;background:#fff}
.brand{left:83px;top:16px;display:flex;align-items:center;gap:8px}
.brand-dot{width:34px;height:34px;border-radius:50%;background:var(--blue)}
.brand-name{font-family:"Bitter",serif;font-size:20px;font-weight:500;color:var(--navy)}
.nav{left:396px;top:30px;display:flex;font-family:"Bitter",serif;font-size:9px;color:#222}
.nav span{padding:0 0;}
.nav .sep{width:1px;height:10px;background:#ccc;margin:0 18px}
.hero{left:0;top:65px;width:756px;height:298px;background:linear-gradient(180deg,#4aa4e6 0%,#bfe2f7 45%,#c79a6e 62%,#3f86c4 80%,#1f5f99 100%)}
.hero-caption{left:124px;top:299px;width:507px;height:44px;background:rgba(20,20,20,.82);color:#fff;font-family:"Oswald",sans-serif;font-size:19px;text-align:center;line-height:44px}
.section-title{width:756px;left:0;text-align:center;font-family:"Bitter",serif;font-size:20px;color:var(--navy);letter-spacing:1px}
.section-sub{width:756px;left:0;text-align:center;font-family:"Bitter",serif;font-size:10px;color:var(--green);letter-spacing:.8px}
.rule{left:83px;width:590px;height:1px;background:var(--rule)}
.lead{left:83px;width:590px;text-align:center;font-size:8.5px;font-weight:700;color:#222}
.para{left:96px;width:564px;text-align:center;font-size:8.5px;line-height:12.4px}
.btn{display:block;background:var(--blue);color:#fff;font-size:8.5px;text-align:center;line-height:20px;height:20px;border-radius:2px}
.services{left:0;top:583px;width:756px;height:212px;background:var(--band)}
.card{top:600px;width:138px;height:177px;background:#fff}
.card-photo{position:absolute;left:2px;top:3px;width:134px;height:75px}
.card-title{position:absolute;top:88px;width:100%;text-align:center;font-family:"Bitter",serif;font-size:12px;color:#111;letter-spacing:.3px}
.card-text{position:absolute;top:110px;width:100%;text-align:center;font-size:8.5px;line-height:14px}
.card .btn{position:absolute;left:36px;top:146px;width:66px}
.quote{top:894px;width:268px;height:74px;border:1px solid #d6d6d6;border-radius:4px;background:#fff}
.quote-tail{position:absolute;left:24px;top:72px}
.avatar{position:absolute;left:9px;top:10px;width:56px;height:56px;border-radius:50%;border:2px solid #ddd}
.quote-text{position:absolute;left:74px;top:13px;width:186px;font-size:8.3px;line-height:12.5px;color:#222}
.quote-mark{color:#bbb;font-family:"Bitter",serif;font-size:14px;line-height:8px;margin-right:3px}
.client{top:990px;font-size:8px;font-weight:700;color:#15184a}
.footer{left:0;top:1028px;width:756px;height:145px;background:var(--blue);color:#fff}
.footer-bar{left:0;top:1173px;width:756px;height:27px;background:var(--blue-dark);color:#fff;font-size:8px;text-align:center;line-height:27px}
.col-title{top:1043px;font-family:"Bitter",serif;font-size:11px;color:#fff}
.col-rule{top:1063px;height:1px;background:rgba(255,255,255,.25)}
.f-item{font-size:8px;color:#fff;display:flex;align-items:center;gap:8px}
.f-item svg{flex:none}
.email-field{left:393px;top:1103px;width:127px;height:20px;background:#fff;border-radius:2px;font-size:7px;color:#777;padding-left:6px;line-height:20px}
.subscribe{left:393px;top:1132px;width:61px;height:20px;background:#0b4f92;color:#fff;font-size:8px;text-align:center;line-height:20px;border-radius:2px}
.social-dot{width:14px;height:14px;border-radius:50%;background:#fff}
</style>
</head>
<body>
<header class="header abs">
  <div class="brand abs"><span class="brand-dot"></span><span class="brand-name">Brivane Management</span></div>
  <nav class="nav abs"><span>HOME</span><span class="sep"></span><span>ABOUT US</span><span class="sep"></span><span>SERVICES</span><span class="sep"></span><span>CONTACT US</span></nav>
</header>

<div class="hero abs" role="img" aria-label="World landmarks standing on a globe under a blue sky with airplanes"></div>
<div class="hero-caption abs">WE PROVIDES MANAGEMENT CONSULTING TO THE TRAVEL INDUSTRY.</div>

<h1 class="section-title abs" style="top:391px;font-weight:400">WELCOME BRIVANE</h1>
<p class="section-sub abs" style="top:417px">STRATEGY MANAGEMENT, INC.</p>
<div class="rule abs" style="top:441px"></div>
<p class="lead abs" style="top:454px">Lorem ipsum dolor sit amet, consectetur adipisicing elit, sed do eiusmod tem incididunt ut labore et dolore magna aliqua. Ut enim ad minim veniam.</p>
<p class="para abs" style="top:473px">Duis aute irure dolor in reprehenderitnin voliuptate velit esse cillum dolore eu fugiat nulla pariatur Excepteur sint occaecat cupidatat non proident, sunt in culpa qui officia deserunt mollit anim id est laborum Neque porro quisquam est, qui dolorem ipsum qus consectetur adipisci velit, sed quia non numquam eius modi tempora incidunt ut labore et dol magnam aliquam quaerat voluptatem. Ut enim ad minima veniam, quis nostrum exer ullam corporis suscipit laboriosam nisi ut aliquid ex ea commodi consequatur.</p>
<a class="btn abs" style="left:346px;top:533px;width:65px">READ MORE</a>

<section class="services abs"></section>
<div class="card abs" style="left:83px">
  <div class="card-photo" role="img" aria-label="Business people shaking hands in an office" style="background:linear-gradient(135deg,#dfe6ef,#2a3242)"></div>
  <h2 class="card-title" style="font-weight:400">Account Management</h2>
  <p class="card-text">Duis aute irure dolor in rderi<br>voliuptate velit esse.</p>
  <a class="btn">READ MORE</a>
</div>
<div class="card abs" style="left:233px">
  <div class="card-photo" role="img" aria-label="Row of business travellers standing with luggage" style="background:linear-gradient(180deg,#e8eef4,#3a3f4a)"></div>
  <h2 class="card-title" style="font-weight:400">Traveller Tools</h2>
  <p class="card-text">Duis aute irure dolor in rderi<br>voliuptate velit esse.</p>
  <a class="btn">READ MORE</a>
</div>
<div class="card abs" style="left:384px">
  <div class="card-photo" role="img" aria-label="Calculator, pen and financial chart" style="background:linear-gradient(135deg,#5b7fb8,#dfe8f5)"></div>
  <h2 class="card-title" style="font-weight:400">Expense Management</h2>
  <p class="card-text">Duis aute irure dolor in rderi<br>voliuptate velit esse.</p>
  <a class="btn">READ MORE</a>
</div>
<div class="card abs" style="left:535px">
  <div class="card-photo" role="img" aria-label="Traveller pulling a suitcase through an airport terminal" style="background:linear-gradient(180deg,#b9c8d8,#5d7088)"></div>
  <h2 class="card-title" style="font-weight:400">Travel Programs</h2>
  <p class="card-text">Duis aute irure dolor in rderi<br>voliuptate velit esse.</p>
  <a class="btn">READ MORE</a>
</div>

<h2 class="section-title abs" style="top:823px;font-weight:400">CLIENT TESTIMONIALS</h2>
<p class="section-sub abs" style="top:849px">NEQUE PORRO QUISQUA MOLOREM</p>
<div class="rule abs" style="top:872px"></div>

<div class="quote abs" style="left:100px">
  <div class="avatar" role="img" aria-label="Portrait of a client" style="background:linear-gradient(180deg,#e9c9a6,#c98f5e)"></div>
  <p class="quote-text"><span class="quote-mark">&ldquo;</span>Lorem ipsu donlor amet, consecte admsicn elt sed do eiusmod tempor incididunt utboret dolorie magna aliqua. Ut enim ad minienia quis nosinttrud exercitation ullamco laboriisi.</p>
  <svg class="quote-tail" width="16" height="10" viewBox="0 0 16 10"><path d="M0 1 L4 9 L14 1" fill="#fff" stroke="#d6d6d6"/></svg>
</div>
<p class="client abs" style="left:100px">Miss. Client Name</p>

<div class="quote abs" style="left:387px">
  <div class="avatar" role="img" aria-label="Portrait of a client" style="background:linear-gradient(180deg,#eef1f5,#8a9ab0)"></div>
  <p class="quote-text"><span class="quote-mark">&ldquo;</span>Lorem ipsu donlor amet, consecte admsicn elt sed do eiusmod tempor incididunt utboret dolorie magna aliqua. Ut enim ad minienia quis nosinttrud exercitation ullamco laboriisi.</p>
  <svg class="quote-tail" width="16" height="10" viewBox="0 0 16 10"><path d="M0 1 L4 9 L14 1" fill="#fff" stroke="#d6d6d6"/></svg>
</div>
<p class="client abs" style="left:387px">Mr. Client Name</p>

<footer class="footer abs"></footer>
<h3 class="col-title abs" style="left:83px;font-weight:400">Quick Links</h3>
<div class="col-rule abs" style="left:83px;width:97px"></div>
<div class="abs" style="left:83px;top:1073px;display:grid;row-gap:12px">
  <span class="f-item"><svg width="6" height="6" viewBox="0 0 6 6"><path d="M0 3h5M3 1l2 2-2 2" stroke="#fff" fill="none"/></svg>Home</span>
  <span class="f-item"><svg width="6" height="6" viewBox="0 0 6 6"><path d="M0 3h5M3 1l2 2-2 2" stroke="#fff" fill="none"/></svg>About Us</span>
  <span class="f-item"><svg width="6" height="6" viewBox="0 0 6 6"><path d="M0 3h5M3 1l2 2-2 2" stroke="#fff" fill="none"/></svg>Services</span>
  <span class="f-item"><svg width="6" height="6" viewBox="0 0 6 6"><path d="M0 3h5M3 1l2 2-2 2" stroke="#fff" fill="none"/></svg>Contact Us</span>
</div>

<h3 class="col-title abs" style="left:208px;font-weight:400">Contact Information</h3>
<div class="col-rule abs" style="left:208px;width:157px"></div>
<div class="f-item abs" style="left:208px;top:1073px;align-items:flex-start">
  <svg width="9" height="11" viewBox="0 0 9 11"><path d="M4.5 0a4 4 0 0 0-4 4c0 3 4 7 4 7s4-4 4-7a4 4 0 0 0-4-4z" fill="#fff"/><circle cx="4.5" cy="4" r="1.5" fill="#0a6fc2"/></svg>
  <span style="margin-left:2px;line-height:11px"><b>BRIVANE</b><br>00 Neque porro quisquam dolor<br>qus consectetur. 000 000</span>
</div>
<div class="f-item abs" style="left:208px;top:1118px"><svg width="9" height="10" viewBox="0 0 9 10"><path d="M2 0l2 2-1 2c1 1 2 2 3 3l2-1 1 2-2 2C3 9 0 5 0 2z" fill="#fff"/></svg><span style="margin-left:2px">(123) 456 7890</span></div>
<div class="f-item abs" style="left:208px;top:1138px"><svg width="10" height="7" viewBox="0 0 10 7"><rect width="10" height="7" fill="#fff"/><path d="M0 0l5 4 5-4" stroke="#0a6fc2" fill="none"/></svg><span style="margin-left:1px">info@brivane-mail.com</span></div>

<h3 class="col-title abs" style="left:393px;font-weight:400">Newsletter Sign Up</h3>
<div class="col-rule abs" style="left:393px;width:127px"></div>
<p class="abs" style="left:393px;top:1073px;width:140px;font-size:8px;line-height:11px;color:#fff">Lorem ipsudolor sit coec adipiscing elitsite amet</p>
<div class="email-field abs">Your Email</div>
<div class="subscribe abs">SUBSCRIBE</div>

<h3 class="col-title abs" style="left:562px;font-weight:400">Follow Us</h3>
<div class="col-rule abs" style="left:562px;width:111px"></div>
<div class="abs" style="left:565px;top:1076px;display:grid;row-gap:9px">
  <span class="f-item"><span class="social-dot"></span>Friendwall</span>
  <span class="f-item"><span class="social-dot"></span>Chirpline</span>
  <span class="f-item"><span class="social-dot"></span>Circleplus</span>
</div>

<div class="footer-bar abs">&copy; 2014 Brivane. All Right reserved.</div>
</body>
</html>
```